Residential Remodeling Contractor needs updated business card

I need a new design for my business card.
Name of the company is Ridgefell Construction. I need a card that commands presence, strength, integrity. I have been in business for 28 years. I am a Residential Remodeling Contractor that covers all aspects of a residential remodel and build.

```html
<!DOCTYPE html>
<html lang="en">
<head>
<meta charset="utf-8">
<title>Ridgefell Construction – Business Card</title>
<link rel="stylesheet" href="https://fonts.googleapis.com/css2?family=Arimo:wght@400&family=Cinzel:wght@700&display=swap">
<style>
  :root {
    --navy: #173e7e;
    --navy-deep: #1d3877;
    --ink: #3a3a3a;
    --paper: #ffffff;
    --backdrop: #eceef1;
    --pattern-light: #6f8fc8;
  }
  * { box-sizing: border-box; margin: 0; padding: 0; }
  html, body {
    width: 1200px; height: 1059px; overflow: hidden;
    background: var(--backdrop);
  }
  .canvas { position: relative; width: 1200px; height: 1059px; }

  .card {
    position: absolute; width: 690px; height: 392px;
    border-radius: 24px; overflow: hidden;
  }
  .card--front { left: 255px; top: 89px; background: var(--paper); box-shadow: 0 2px 10px rgba(0,0,0,.12); }
  .card--back { left: 255px; top: 569px; background: var(--navy-deep); }

  .wordmark {
    position: absolute; display: flex; align-items: center; gap: 12px;
    font-family: "Cinzel", "Times New Roman", serif; font-weight: 700;
    line-height: 1.05; letter-spacing: .5px;
  }
  .wordmark__square { width: 26px; height: 26px; flex: none; }
  .wordmark__text { display: block; }
  .card--front .wordmark { left: 70px; top: 160px; color: var(--navy); font-size: 27px; }
  .card--front .wordmark__square { background: var(--navy); }
  .card--back .wordmark { left: 446px; top: 268px; color: var(--paper); font-size: 19px; gap: 9px; }
  .card--back .wordmark__square { background: var(--paper); width: 18px; height: 18px; }

  .divider {
    position: absolute; left: 344px; top: 119px; width: 1.5px; height: 150px;
    background: var(--navy);
  }

  .person { position: absolute; left: 371px; top: 113px; }
  .person__name {
    font-family: "Cinzel", "Times New Roman", serif; font-weight: 700;
    color: var(--navy); font-size: 21px; letter-spacing: .3px; line-height: 1.2;
  }
  .person__title {
    font-family: "Arimo", Arial, sans-serif; color: var(--ink);
    font-size: 15.5px; margin-top: 1px;
  }

  .contacts {
    position: absolute; left: 371px; top: 178px; list-style: none;
    font-family: "Arimo", Arial, sans-serif; font-size: 16.5px; color: var(--ink);
  }
  .contacts li { display: flex; align-items: center; height: 24.5px; }
  .contacts svg { width: 13px; height: 13px; margin-right: 9px; fill: var(--navy); flex: none; }
  .contacts .accent { color: var(--navy); }

  .address-band {
    position: absolute; left: 0; top: 327px; width: 100%; height: 31px;
    background: var(--navy); color: var(--paper);
    font-family: "Arimo", Arial, sans-serif; font-size: 16px;
    display: flex; align-items: center; justify-content: center;
  }

  .back-pattern {
    position: absolute; inset: 0;
    background: linear-gradient(200deg, var(--pattern-light) 0%, #3a5a9e 35%, var(--navy-deep) 70%);
  }
</style>
</head>
<body>
<div class="canvas">

  <section class="card card--front">
    <div class="wordmark">
      <span class="wordmark__square"></span>
      <span class="wordmark__text">Ridgefell<br>Construction</span>
    </div>

    <div class="divider"></div>

    <div class="person">
      <div class="person__name">DANIEL OSTRANDER</div>
      <div class="person__title">Owner &amp; Manager</div>
    </div>

    <ul class="contacts">
      <li>
        <svg viewBox="0 0 16 16" aria-hidden="true"><path d="M1 6c0-2 3-3 7-3s7 1 7 3v1h-3V5.5H4V7H1zM3 8h10l1 6H2z"/></svg>
        555 214 7730
      </li>
      <li>
        <svg viewBox="0 0 16 16" aria-hidden="true"><path d="M4 0h8a1 1 0 0 1 1 1v14a1 1 0 0 1-1 1H4a1 1 0 0 1-1-1V1a1 1 0 0 1 1-1zm1 2v10h6V2zm3 11a1 1 0 1 0 0 2 1 1 0 0 0 0-2z"/></svg>
        555-318-40926
      </li>
      <li>
        <svg viewBox="0 0 16 16" aria-hidden="true"><path d="M8 1l7 5v9H1V6zm0 2L3 6.5 8 10l5-3.5z"/></svg>
        info@ridgefellconstruction.com
      </li>
      <li>
        <svg viewBox="0 0 16 16" aria-hidden="true"><circle cx="8" cy="8" r="7"/><path d="M5 4c2 0 2 2 4 2s1 3-1 3-1 3-3 3" fill="none" stroke="#fff" stroke-width="1.3"/></svg>
        <span>www.<span class="accent">ridgefellconstruction</span>.com</span>
      </li>
    </ul>

    <div class="address-band">P.O. Box&nbsp; Street Name Country Name AB, A5B 521</div>
  </section>

  <section class="card card--back">
    <div class="back-pattern" role="img" aria-label="Repeating pattern of brand symbols fading from dark navy to light blue"></div>
    <div class="wordmark">
      <span class="wordmark__square"></span>
      <span class="wordmark__text">Ridgefell<br>Construction</span>
    </div>
  </section>

</div>
</body>
</html>
```